Refresh of a Media Kit for Adtech Company - Needs jazzing up!

We have a Media Kit that's too ugly and boring to send to clients. Attaching some examples of ones we like better. Keep the general styling and theme of the current media kit (it's our brand style) and all the information conveyed, but please change anything and everything else to make it more dynamic. Attaching examples of media kits we like.

The "Media Kit Vantor" is the one you're designing, the others are just examples of media kits we liked.
Updates

Here's a link to "Glamour Shots" that can be used as appropriate throughout the Media kit: https://www.filquarry.net/sh/q7mzkx31rwp8tnb/BXK4Pqwertz_LM9nVwYdQaHfZ?dl=0

Target Market(s)

Demand partners

Colors
0592cd
85cae6
34a7d8

Requirements
Nice to have
• Here are some glamour shots you can use if you see a good fit for any of them: https://www.filquarry.net/sh/q7mzkx31rwp8tnb/BXK4Pqwertz_LM9nVwYdQaHfZ?dl=0

```html
<!DOCTYPE html>
<html lang="en">
<head>
<meta charset="utf-8">
<title>Vantor Media Kit – Page 5</title>
<link href="https://fonts.googleapis.com/css2?family=Roboto:wght@300;400;500;700&display=swap" rel="stylesheet">
<style>
  :root {
    --sheet: #e6e6e6;
    --paper: #ffffff;
    --ink: #1c1c1c;
    --ink-soft: #3a3a3a;
    --brand-light: #5bbde3;
    --brand-pale: #85cae6;
    --brand: #1a9ad6;
    --brand-deep: #0592cd;
    --bright-blue: #068fff;
    --bar: #5fb9f7;
    --cell: #eeeeee;
    --rule: #dcdcdc;
    --halo: #dfeaf6;
    --page-num: #8a8a8a;
  }
  * { box-sizing: border-box; margin: 0; padding: 0; }
  html, body { width: 1200px; height: 724px; overflow: hidden; }
  body {
    background: var(--sheet);
    font-family: "Roboto", Arial, sans-serif;
    color: var(--ink);
    position: relative;
  }
  .slide {
    position: absolute;
    width: 544px;
    height: 306px;
    background: var(--paper);
    overflow: hidden;
  }
  .slide--competitors { left: 39px; top: 40px; }
  .slide--formats { left: 617px; top: 40px; }
  .slide--thanks { left: 39px; top: 377px; background: var(--bright-blue); }

  .slide-title {
    position: absolute;
    left: 22px;
    top: 30px;
    font-size: 20.5px;
    line-height: 24.5px;
    font-weight: 300;
    color: var(--ink);
    letter-spacing: 0.1px;
  }
  .slide-title .series { color: var(--brand-light); font-weight: 700; }
  .slide-title .divider { color: var(--brand-light); font-weight: 300; }
  .slide-title strong { font-weight: 700; }

  /* Comparison table */
  .feature-grid {
    position: absolute;
    left: 23px;
    top: 130px;
    display: grid;
    grid-template-columns: 67px repeat(4, 54px);
    grid-auto-rows: 19px;
    column-gap: 1.5px;
    row-gap: 1.5px;
    font-size: 10.5px;
    font-weight: 300;
  }
  .feature-grid .head {
    text-align: center;
    line-height: 19px;
    color: var(--ink);
  }
  .feature-grid .cell {
    background: var(--cell);
    text-align: center;
    line-height: 19px;
    font-size: 8px;
    color: var(--ink);
  }
  .feature-grid .name {
    background: var(--cell);
    line-height: 19px;
    padding-left: 4px;
    font-size: 10.5px;
    color: var(--ink);
  }
  .feature-grid .name--own { color: var(--brand); text-align: center; padding-left: 0; }
  .feature-grid .cell--own { color: var(--brand); }

  .column-rule {
    position: absolute;
    left: 339px;
    top: 88px;
    width: 1px;
    height: 187px;
    background: var(--rule);
  }
  .diagram-label {
    position: absolute;
    left: 352px;
    font-size: 10.5px;
    font-weight: 300;
    color: var(--ink);
    letter-spacing: 0.1px;
  }
  .diagram-label strong { font-weight: 700; }
  .diagram-label::after {
    content: "";
    position: absolute;
    left: 0;
    top: 16px;
    width: 71px;
    height: 3px;
    background: var(--brand-pale);
  }
  .diagram-label--ours { top: 96px; }
  .diagram-label--theirs { top: 186px; }

  .brand-tag {
    position: absolute;
    right: 11px;
    bottom: 7px;
    display: flex;
    align-items: center;
    gap: 3px;
    font-size: 7.5px;
    font-weight: 700;
    color: var(--brand);
  }
  .brand-tag .mark {
    width: 10px;
    height: 10px;
    border-radius: 2px;
    background: var(--brand);
  }
  .brand-tag--light { color: #ffffff; }
  .brand-tag--light .mark { background: #ffffff; }

  /* Formats slide */
  .halo {
    position: absolute;
    left: 296px;
    top: 100px;
    width: 270px;
    height: 270px;
    border-radius: 50%;
    background: var(--halo);
  }
  .halo-lines {
    position: absolute;
    left: 296px;
    width: 270px;
    top: 178px;
    text-align: center;
    color: #ffffff;
    font-size: 19px;
    font-weight: 300;
    line-height: 32.5px;
  }
  .spec-column { position: absolute; top: 72px; }
  .spec-column h3 {
    font-size: 9.5px;
    font-weight: 500;
    color: var(--ink);
    margin-bottom: 6px;
    white-space: nowrap;
  }
  .spec-column ul { list-style: none; }
  .spec-column li {
    position: relative;
    padding-left: 12px;
    font-size: 8px;
    line-height: 9.5px;
    font-weight: 300;
    color: var(--ink-soft);
  }
  .spec-column li::before {
    content: "✓";
    position: absolute;
    left: 0;
    top: 0;
    color: var(--brand);
    font-weight: 700;
  }
  .spec-column--network { left: 34px; width: 126px; }
  .spec-column--network ul { width: 92px; }
  .spec-column--content { left: 132px; }
  .spec-column--content ul { width: 80px; }
  .spec-column--play { left: 251px; }

  /* Thank you slide */
  .thanks-title {
    position: absolute;
    left: 57px;
    top: 135px;
    font-size: 44px;
    line-height: 50px;
    font-weight: 400;
    color: #ffffff;
    letter-spacing: -0.3px;
  }
  .thanks-title strong { font-weight: 700; }
  .thanks-bar {
    position: absolute;
    left: 58px;
    top: 204px;
    width: 137px;
    height: 5px;
    background: var(--bar);
  }

  .page-number {
    position: absolute;
    right: 14px;
    bottom: 8px;
    font-size: 36px;
    font-weight: 700;
    color: var(--page-num);
  }
</style>
</head>
<body>

  <section class="slide slide--competitors">
    <h2 class="slide-title"><span class="series">DOOH NOW</span> <span class="divider">|</span> Your <strong>Competitors;</strong> Our competitors<br>are trash, emphasize own inventory</h2>

    <div class="feature-grid" role="table" aria-label="Feature comparison">
      <div class="head"></div>
      <div class="head">Feature 1</div>
      <div class="head">Feature 1</div>
      <div class="head">Feature 3</div>
      <div class="head">Feature 4</div>

      <div class="name name--own">AdHarbor</div>
      <div class="cell cell--own">✓</div>
      <div class="cell cell--own">✓</div>
      <div class="cell cell--own">✓</div>
      <div class="cell cell--own">✓</div>

      <div class="name">Competitor 1</div>
      <div class="cell">✓</div>
      <div class="cell">✓</div>
      <div class="cell"></div>
      <div class="cell"></div>

      <div class="name">Competitor 2</div>
      <div class="cell"></div>
      <div class="cell">✓</div>
      <div class="cell">✓</div>
      <div class="cell"></div>

      <div class="name">Competitor 3</div>
      <div class="cell">✓</div>
      <div class="cell">✓</div>
      <div class="cell">✓</div>
      <div class="cell"></div>
    </div>

    <div class="column-rule"></div>
    <div class="diagram-label diagram-label--ours">DIAGRAM OF OUR <strong>SYSTEM</strong></div>
    <div class="diagram-label diagram-label--theirs">DIAGRAM OF THEIR <strong>SYSTEM</strong></div>

    <div class="brand-tag"><span class="mark"></span>AdHarbor</div>
  </section>

  <section class="slide slide--formats">
    <h2 class="slide-title"><span class="series">DOOH NOW</span> <span class="divider">|</span> Digital Media <strong>Formats</strong></h2>

    <div class="halo"></div>
    <div class="halo-lines">The Right Time.<br>The Right Message.<br>The Right Audience.</div>

    <div class="spec-column spec-column--network">
      <h3>Network</h3>
      <ul>
        <li>Indoor, 32 –73” Screens</li>
        <li>Full Screen Take Over</li>
        <li>50% loop reservation for ads</li>
        <li>Exclusively sold programmatically</li>
        <li>No Blacklisted Advertisers</li>
        <li>Approval Upon Venue Review</li>
        <li>Static ($5.5 CPM) &amp; Video ($6.5 CPM)</li>
      </ul>
    </div>

    <div class="spec-column spec-column--content">
      <h3>Content Specifications</h3>
      <ul>
        <li>1920 pixels (w) x 1080 pixels (h) 16:9</li>
        <li>1080 pixels (w) x 1920 pixels (h) 9:16</li>
        <li>Static: PNG, RGB, encoded. JPG or H.264</li>
        <li>Video: .MP$ / encoded .MOV</li>
      </ul>
    </div>

    <div class="spec-column spec-column--play">
      <h3>Ad Content Play Suggestions</h3>
      <ul>
        <li>15 second</li>
        <li>30 second</li>
        <li>60 second</li>
      </ul>
    </div>

    <div class="brand-tag brand-tag--light"><span class="mark"></span>AdHarbor</div>
  </section>

  <section class="slide slide--thanks">
    <h2 class="thanks-title">Thank <strong>you.</strong></h2>
    <div class="thanks-bar"></div>
  </section>

  <div class="page-number">5</div>

</body>
</html>
```